Every Shelf Set Neatly or ESN Organized needs a business card design. ESN Organized is a professi

We need a business card design that is clean, sharp and conveys a sense of organization. I already have a logo.

Target Market(s)

Families (specifically mothers), small business owners, parents, seniors

Industry/Entity Type

Business

Contact Information for Business Card

My website is www.esnorganized-example.com and my Facebook page is http://www.sociallink-example.com/everyshelfsetneatly. The phone number is 418-552-7094 and I want to be listed as Lorna M. Pelham, Owner

Requirements
Must have
• My logo.

```html
<!DOCTYPE html>
<html lang="en">
<head>
<meta charset="utf-8">
<title>ESN Organized – Business Card</title>
<link rel="stylesheet" href="https://fonts.googleapis.com/css2?family=Open+Sans:wght@400;600&display=swap">
<style>
  :root {
    --page-bg: #e9e7e3;
    --card-dark: #0b0b0c;
    --card-mid: #2a2a2c;
    --name-blue: #2f6fd6;
    --text-light: #d8d8d8;
    --icon-blue: #3f7fd8;
    --frost-top: #d9dde2;
    --frost-bottom: #c9ccd0;
    --logo-ink: #1c2738;
  }
  html, body {
    margin: 0;
    width: 1200px;
    height: 969px;
    overflow: hidden;
    background: var(--page-bg);
    font-family: "Open Sans", Arial, sans-serif;
  }
  .card {
    position: absolute;
    left: 100px;
    top: 200px;
    width: 1000px;
    height: 570px;
    background: radial-gradient(ellipse at 35% 40%, var(--card-mid) 0%, var(--card-dark) 70%);
    overflow: hidden;
    box-shadow: 0 12px 30px rgba(0,0,0,0.25);
  }
  .frost-panel {
    position: absolute;
    inset: 0;
  }
  .identity {
    position: absolute;
    left: 72px;
    top: 88px;
  }
  .identity .name {
    margin: 0;
    font-size: 34px;
    font-weight: 600;
    letter-spacing: 0.5px;
    color: var(--name-blue);
    text-transform: uppercase;
  }
  .identity .role {
    margin: 4px 0 0;
    font-size: 25px;
    color: var(--text-light);
    text-transform: uppercase;
  }
  .contacts {
    position: absolute;
    left: 72px;
    top: 370px;
    margin: 0;
    padding: 0;
    list-style: none;
  }
  .contacts li {
    display: flex;
    align-items: center;
    height: 37px;
    font-size: 22px;
    color: var(--text-light);
    white-space: nowrap;
  }
  .contacts svg {
    width: 20px;
    height: 20px;
    margin-right: 11px;
    flex: none;
  }
  .brand-name {
    position: absolute;
    left: 572px;
    top: 432px;
    display: flex;
    align-items: center;
    gap: 14px;
    font-size: 40px;
    font-weight: 600;
    color: var(--logo-ink);
    white-space: nowrap;
  }
  .brand-name .mark {
    width: 26px;
    height: 26px;
    background: var(--logo-ink);
  }
</style>
</head>
<body>
  <div class="card">
    <svg class="frost-panel" viewBox="0 0 1000 570" width="1000" height="570">
      <defs>
        <linearGradient id="frost" x1="0" y1="0" x2="0" y2="1">
          <stop offset="0" stop-color="var(--frost-top)"/>
          <stop offset="1" stop-color="var(--frost-bottom)"/>
        </linearGradient>
      </defs>
      <path d="M772 0 H1000 V570 H500 Q442 570 466 518 L708 44 Q730 0 772 0 Z" fill="url(#frost)" opacity="0.92"/>
    </svg>

    <div class="identity">
      <p class="name">Lorna M. Pelham</p>
      <p class="role">Owner</p>
    </div>

    <ul class="contacts">
      <li>
        <svg viewBox="0 0 24 24"><path fill="var(--icon-blue)" d="M6.6 10.8a15.1 15.1 0 0 0 6.6 6.6l2.2-2.2a1 1 0 0 1 1-.25 11.4 11.4 0 0 0 3.6.57 1 1 0 0 1 1 1V20a1 1 0 0 1-1 1A17 17 0 0 1 3 4a1 1 0 0 1 1-1h3.5a1 1 0 0 1 1 1c0 1.25.2 2.45.57 3.57a1 1 0 0 1-.25 1z"/></svg>
        418-552-7094
      </li>
      <li>
        <svg viewBox="0 0 24 24" fill="none" stroke="var(--icon-blue)" stroke-width="2"><circle cx="12" cy="12" r="10" fill="var(--icon-blue)"/><path d="M2 12h20M12 2c3 3 3 17 0 20M12 2c-3 3-3 17 0 20" stroke="var(--card-dark)" stroke-width="1.5"/></svg>
        www.esnorganized-example.com
      </li>
      <li>
        <svg viewBox="0 0 24 24"><rect x="2" y="2" width="20" height="20" fill="var(--icon-blue)"/></svg>
        everyshelfsetneatly
      </li>
    </ul>

    <div class="brand-name">
      <span class="mark"></span>
      <span>ESN Organized</span>
    </div>
  </div>
</body>
</html>
```